Banner Ad - Online Clothing Store

I have started an Online Clothing Business. I will be hosting pop up stores and pop up parties from home or in other peoples home or workplace. I need a physical Vinyl Banner Design (Vertical) for Indoor Use which will be displayed on a stand near the garment racks of clothing on display.
Size of Banner is 76cm x 244cm (Document Trim Size 76.2 x 242.5 cm
1500 x 4774 pixels Full Bleed Size 76.7 x 243.2 cm
1510 x 4788 pixels). Resolution 50DPI. I am going with a very crisp clean colour scheme of Black or Charcoal Grey with Silver. Require something Modern and trendy, Appealing to women 18-35 but not too girly. I will be mostly stocking clothing but some accessories such as jewellery, bags, clutches and spring racing fascinators and hatinators in the near future. *** I do not want any cartoon type or clip art type pictures at all. Only real life images. Some Brands I stock are Velqora, Trimbex, Dunmarro, Cobalt Reed, Mirela Tosk, Vorlin, Plums + Pebbles, Grey Drawer, Amber Loop, Odd Wren, Nine Pilots, Quill & Marlo, Brisk Muse, 5 Quiet Harbors, Court of Pemberly I have attached the logos of these labels to incorporate into the banner if possible. *** Veradine Wardrobe is the correct spelling and the registered business name so it must not include and other added words. I will attach the logos for labels I stock. I have attached a logo for the business but will have to submit the correct file formats to you in a day or two as im waiting for this to be supplied to me from the designer. I have also included a couple example banners that I have found in a search engine that I like however am open to some other suggestions.
www.veradinewardrobe-example.com.au
www.hello@veradinewardrobe-example.com.au
If you can include the little symbols for facebook and instagram
Updates

Have updated and included the logos of labels I will be stocking to incorporate into the banner. I have also other versions/variations of the business logo if you think one of those would suit better.

Target Market(s)

Appealing to women 18-35 but not too girl

Industry/Entity Type

Clothing

Font styles to use
Sans Serif

Requirements
Nice to have
• You will see attached files of Water Colour Banners. I really like the look of these. Even if they are a opaque or a watermark and not at bold so as to draw too much attention away from the business name 'Veradine Wardrobe' Like i said though I am open to suggestions.

```html
<!DOCTYPE html>
<html lang="en">
<head>
<meta charset="UTF-8">
<title>Veradine Wardrobe – Vertical Banner</title>
<link href="https://fonts.googleapis.com/css2?family=Raleway:wght@400;600;700&display=swap" rel="stylesheet">
<style>
  :root {
    --page-bg: #e9e9ea;
    --banner-bg: #ffffff;
    --charcoal: #3d3d40;
    --silver: #a9abae;
    --pink: #e2457e;
    --pink-deep: #d12f69;
    --grey-text: #6b6c70;
    --petal-yellow: #f2e37a;
    --petal-green: #b9d77a;
    --petal-soft: #f7f5dc;
  }
  * { margin: 0; padding: 0; box-sizing: border-box; }
  html, body {
    width: 900px; height: 1200px; overflow: hidden;
    background: var(--page-bg);
    font-family: "Raleway", sans-serif;
  }
  .canvas {
    width: 900px; height: 1200px;
    display: flex; align-items: center; justify-content: center;
  }
  .banner {
    width: 380px; height: 1160px;
    background: var(--banner-bg);
    position: relative;
    box-shadow: 0 2px 10px rgba(0,0,0,.12);
    display: flex; flex-direction: column; align-items: center;
    padding: 34px 26px 26px;
  }
  .brand-lockup {
    display: flex; align-items: center; gap: 12px;
    align-self: flex-start; margin-left: 8px;
  }
  .brand-mark {
    width: 62px; height: 62px; border-radius: 50%;
    background: var(--charcoal);
  }
  .brand-name {
    font-weight: 600; font-size: 26px; line-height: 1.05;
    color: var(--charcoal);
  }
  .floral-art {
    width: 100%; height: 330px; margin-top: 22px;
    border-radius: 4px;
    background: radial-gradient(ellipse at 40% 45%, var(--petal-yellow) 0%, var(--petal-green) 38%, var(--petal-soft) 70%, var(--banner-bg) 100%);
  }
  .tagline { text-align: center; margin-top: 22px; }
  .tagline-head {
    font-weight: 700; font-size: 25px; color: var(--pink);
  }
  .tagline-sub {
    font-size: 17px; color: var(--grey-text); margin-top: 4px;
  }
  .tagline-brands {
    font-weight: 600; font-size: 17px; color: var(--pink); margin-top: 10px; line-height: 1.3;
  }
  .cta {
    margin-top: 26px; font-weight: 700; font-size: 24px; color: var(--pink-deep);
  }
  .designer-note {
    margin-top: 34px; text-align: center;
    font-weight: 600; font-size: 16px; color: var(--pink); line-height: 1.4;
  }
  .label-grid {
    margin-top: 20px; width: 100%;
    display: grid; grid-template-columns: repeat(3, 1fr);
    row-gap: 18px; column-gap: 8px; align-items: center; justify-items: center;
  }
  .label-name {
    font-weight: 600; font-size: 14px; color: var(--charcoal);
    text-align: center; line-height: 1.1;
  }
  .label-heart { width: 34px; height: 30px; }
  .banner-footer {
    margin-top: auto; width: 100%;
    display: flex; align-items: center; justify-content: space-between;
    border-top: 2px solid var(--silver); padding-top: 12px;
  }
  .footer-url { font-weight: 600; font-size: 12.5px; color: var(--charcoal); }
  .footer-social { display: flex; gap: 6px; }
  .social-chip { width: 18px; height: 18px; background: var(--silver); }
</style>
</head>
<body>
<div class="canvas">
  <div class="banner">
    <div class="brand-lockup">
      <div class="brand-mark"></div>
      <div class="brand-name">Veradine<br>Wardrobe</div>
    </div>

    <div class="floral-art" role="img" aria-label="Soft watercolour flower in yellow and green tones"></div>

    <div class="tagline">
      <p class="tagline-head">Stylish, Trendy and Classy</p>
      <p class="tagline-sub">collection of women clothing and accessories</p>
      <p class="tagline-brands">Brings wide range of brands<br>at your doorstep</p>
    </div>

    <p class="cta">...Just a few clicks away!</p>

    <p class="designer-note">Get wide range of designer's wear.<br>Fabulous collection...</p>

    <div class="label-grid">
      <span class="label-name">Velqora</span>
      <span class="label-name">Trimbex</span>
      <span class="label-name">Dunmarro</span>
      <span class="label-name">Cobalt Reed</span>
      <svg class="label-heart" viewBox="0 0 34 30" aria-hidden="true">
        <path d="M17 29 C5 20 1 14 1 8.5 C1 4 4.5 1 8.7 1 C12 1 15 3 17 6 C19 3 22 1 25.3 1 C29.5 1 33 4 33 8.5 C33 14 29 20 17 29 Z" fill="var(--charcoal)"/>
      </svg>
      <span class="label-name">Mirela Tosk</span>
      <span class="label-name">Vorlin</span>
      <span class="label-name">Plums + Pebbles</span>
      <span class="label-name">Grey Drawer</span>
      <span class="label-name">Amber Loop</span>
      <span class="label-name">Odd Wren</span>
      <span class="label-name">Nine Pilots</span>
    </div>

    <div class="banner-footer">
      <span class="footer-url">www.veradinewardrobe-example.com.au</span>
      <div class="footer-social">
        <span class="social-chip"></span>
        <span class="social-chip"></span>
      </div>
    </div>
  </div>
</div>
</body>
</html>
```